We need a complete design for our construction company KELTO CONSTRUCTION based in Auckland New Zealand, we need a logo, website, business card, vehicle design etc..
We are a mid to high-end construction company who work mostly on residential projects and some commercial.

What we want to see in the design;
Professional,
Architectural,
Simple,
Alternative,

We want the design to communicate professionalism, high quality wormanship and and quality service.

Target Market(s)

People looking for a quality building/ construction company

Industry/Entity Type

Construction Company

Contact Information for Business Card

KELTO CONSTRUCTION.co.nz
Lino Verasek
lino@keltoconstruction.example.nz
021 5807 462

Logo Text

KELTO CONSTRUCTION

Number of Pages Required

5+ page

Font styles to use
Sans Serif

Colors

Designer to choose colors to be used in the design.

Requirements
Must have
• Must appear high end, professional, quality, be simple, easy to use, give security to potential clients
Nice to have
• high-quality photos of our recent projects
• about us page
• blog page
• contact us page
• high quality content
Should not have
• should not be hard to use and have too much going on.

```html
<!DOCTYPE html>
<html lang="en">
<head>
<meta charset="utf-8">
<title>Kelto Construction</title>
<link rel="stylesheet" href="https://fonts.googleapis.com/css2?family=Montserrat:wght@400;500;600;700&family=Arimo:wght@400;700&family=Roboto:wght@400;500&display=swap">
<style>
:root{
  --navy:#13336b;
  --navy-deep:#0f2a5c;
  --gold:#f4b90a;
  --gold-band:rgba(244,185,10,.93);
  --ink:#222;
  --muted:#555;
  --footer-bg:#f2f2f2;
  --white:#fff;
}
*{margin:0;padding:0;box-sizing:border-box}
html,body{width:1200px;height:2586px;overflow:hidden}
body{position:relative;background:var(--white);font-family:"Arimo",Arial,sans-serif;color:var(--ink)}
.abs{position:absolute}
.center{left:0;width:1200px;text-align:center}

/* header */
.site-header{position:absolute;top:0;left:0;width:1200px;height:97px;background:var(--white)}
.brand{position:absolute;left:84px;top:22px;display:flex;align-items:center;gap:10px}
.brand-mark{width:34px;height:34px;background:var(--navy)}
.brand-name{font-family:"Montserrat",sans-serif;font-weight:700;font-size:19px;color:var(--gold);letter-spacing:.2px}
.main-nav{position:absolute;right:86px;top:42px;display:flex;gap:46px;font-family:"Montserrat",sans-serif;font-weight:600;font-size:13px;color:#222}
.main-nav .active{color:var(--gold)}

/* hero */
.hero-photo{position:absolute;left:0;top:97px;width:1200px;height:640px;background:linear-gradient(180deg,#3d5a86 0%,#5a7aa6 35%,#6f8fb6 60%,#4a6590 100%)}
.hero-band{position:absolute;left:0;top:560px;width:1200px;height:380px}
.hero-title{top:302px;font-family:"Montserrat",sans-serif;font-weight:700;font-size:44px;color:var(--gold)}
.hero-sub{top:364px;font-family:"Montserrat",sans-serif;font-weight:500;font-size:25px;color:var(--white)}
.btn{display:block;background:var(--gold);color:var(--white);font-family:"Montserrat",sans-serif;font-weight:700;text-align:center}
.hero-btn{left:528px;top:419px;width:144px;height:45px;line-height:45px;font-size:16px}
.hero-arrow{top:389px;width:36px;height:36px}
.welcome-kicker{top:624px;font-family:"Montserrat",sans-serif;font-size:21px;color:var(--white)}
.welcome-title{top:655px;font-family:"Montserrat",sans-serif;font-weight:600;font-size:31px;color:var(--white)}
.welcome-rule{left:557px;top:703px;width:86px;height:4px;background:var(--navy)}
.welcome-text{top:730px;font-size:12.5px;line-height:26px;color:var(--white)}
.welcome-btn{left:482px;top:837px;width:237px;height:44px;line-height:42px;border:1px solid rgba(255,255,255,.8);background:rgba(150,110,0,.35);color:var(--white);font-family:"Montserrat",sans-serif;font-weight:600;font-size:12.5px;text-align:center}

/* services */
.section-title{font-family:"Montserrat",sans-serif;font-weight:600;font-size:24px}
.services-title{top:980px;color:var(--navy)}
.section-sub{font-size:12.5px}
.services-sub{top:1025px;color:var(--muted)}
.service{position:absolute;top:1080px;width:300px;text-align:center}
.service-icon{display:block;margin:0 auto;width:122px;height:122px}
.service-name{margin-top:24px;font-family:"Montserrat",sans-serif;font-weight:600;font-size:18px;color:var(--navy)}
.service-text{margin-top:12px;font-size:12.5px;line-height:25px;color:var(--muted)}

/* projects */
.projects-bg{position:absolute;left:0;top:1383px;width:1200px;height:448px;background:linear-gradient(180deg,#2b3032 0%,#363c3d 50%,#2a2e30 100%)}
.projects-title{top:1418px;color:var(--white)}
.projects-sub{top:1459px;color:var(--white)}
.project-card{position:absolute;top:1512px;width:246px;height:257px;background:var(--white)}
.project-photo{width:246px;height:191px}
.project-caption{position:relative;height:66px;padding:18px 0 0 12px}
.project-name{font-family:"Montserrat",sans-serif;font-weight:600;font-size:13px;color:var(--ink)}
.project-meta{margin-top:4px;font-size:13px;color:var(--ink)}
.project-plus{position:absolute;right:0;top:0;width:58px;height:66px;background:var(--gold)}
.slider-arrow{top:1603px;width:24px;height:80px}

/* about */
.about-photo{left:133px;top:1890px;width:450px;height:300px;background:linear-gradient(120deg,#e9e4dc 0%,#f1d6c4 40%,#e86a3a 75%,#c95a33 100%)}
.about-title{left:633px;top:1898px;color:var(--navy)}
.about-kicker{left:633px;top:1942px;font-family:"Montserrat",sans-serif;font-weight:600;font-size:13px;color:var(--gold)}
.about-text{left:634px;top:1973px;width:450px;font-size:12px;line-height:26px;color:var(--muted);white-space:nowrap}
.about-btn{left:634px;top:2121px;width:130px;height:43px;line-height:43px;font-size:15px}

/* footer */
.site-footer{position:absolute;left:0;top:2259px;width:1200px;height:265px;background:var(--footer-bg)}
.footer-col{position:absolute;top:2305px}
.footer-heading{font-family:"Roboto",sans-serif;font-weight:500;font-size:17px;color:#333;margin-bottom:16px}
.link-list{list-style:none;font-size:13px;color:#333}
.link-list li{height:30px;display:flex;align-items:center}
.link-list li svg{margin-right:14px}
.contact-list{list-style:none;font-size:13px;color:#555}
.contact-list li{display:flex;align-items:flex-start;margin-bottom:13px;line-height:16px}
.contact-list li svg{flex:none;margin-right:11px;margin-top:2px}
.contact-list a{color:#555}
.footer-text{font-size:13px;line-height:21px;color:#555}
.newsletter-input{margin-top:16px;width:212px;height:32px;border:1px solid #ccc;background:var(--white);font-size:12.5px;color:#444;padding:8px 0 0 14px}
.subscribe-btn{margin-top:8px;width:81px;height:29px;line-height:29px;font-family:"Montserrat",sans-serif;font-weight:500;font-size:11px}
.socials{display:flex;gap:5px;margin-top:17px}
.social{width:38px;height:38px;border:1.5px solid #9aa0a6;border-radius:50%}
.bottom-bar{position:absolute;left:0;top:2524px;width:1200px;height:62px;background:var(--navy-deep)}
.copyright{top:2547px;font-size:13px;color:var(--white)}
</style>
</head>
<body>

<header class="site-header">
  <div class="brand"><span class="brand-mark"></span><span class="brand-name">KELTO CONSTRUCTION</span></div>
  <nav class="main-nav">
    <span class="active">HOME</span><span>ABOUT US</span><span>PROJECTS</span><span>BLOG</span><span>CONTACT US</span>
  </nav>
</header>

<section class="hero">
  <div class="hero-photo" role="img" aria-label="Auckland city skyline at dusk with towers and high-rise buildings"></div>
  <svg class="hero-band" viewBox="0 560 1200 380" width="1200" height="380">
    <polygon points="0,721 600,569 1200,721 1200,737 0,737" fill="var(--gold-band)"/>
    <polygon points="0,737 1200,737 1200,831 600,931 0,831" fill="var(--gold)"/>
  </svg>
  <h1 class="abs center hero-title">KELTO CONSTRUCTION</h1>
  <p class="abs center hero-sub">CONSTRUCTION COMPANY IN AUCKLAND, NEWZEALAND</p>
  <a class="abs btn hero-btn">READ MORE</a>
  <svg class="abs hero-arrow" style="left:41px" viewBox="0 0 36 36"><circle cx="18" cy="18" r="16" fill="none" stroke="#fff" stroke-width="1.6"/><polyline points="20,12 14,18 20,24" fill="none" stroke="#fff" stroke-width="2"/></svg>
  <svg class="abs hero-arrow" style="left:1124px" viewBox="0 0 36 36"><circle cx="18" cy="18" r="16" fill="none" stroke="#fff" stroke-width="1.6"/><polyline points="16,12 22,18 16,24" fill="none" stroke="#fff" stroke-width="2"/></svg>

  <p class="abs center welcome-kicker">WELCOME TO</p>
  <h2 class="abs center welcome-title">KELTO CONSTRUCTION</h2>
  <div class="abs welcome-rule"></div>
  <p class="abs center welcome-text">Sed ut perspiciatis unde omnis iste natus error sit voluptatem accusantium doloremque laudantium, totam rem aperiam,<br>eaque ipsa quae ab illo inventore veritatis et quasi architecto beatae vitae dicta sunt explicabo. Nemo enim aut odit aut fugit,<br>sed quia consequuntur magni dolores eos qui ratione voluptatem sequi nesciunt.</p>
  <a class="abs welcome-btn">CLICK HERE FOR MORE INFO</a>
</section>

<section class="services">
  <h2 class="abs center section-title services-title">OUR SERVICES</h2>
  <p class="abs center section-sub services-sub">Sed ut perspiciatis unde omnis iste natus error sit voluptatem accusantium doloremque laudantium, totam rem aperiam</p>

  <div class="service" style="left:105px">
    <svg class="service-icon" viewBox="0 0 122 122"><circle cx="61" cy="61" r="59" fill="var(--gold)"/><circle cx="61" cy="61" r="54" fill="var(--navy)"/>
      <polygon points="61,40 39,60 45,60 45,80 77,80 77,60 83,60" fill="#fff"/><rect x="56" y="65" width="10" height="15" fill="var(--navy)"/></svg>
    <h3 class="service-name">RESIDENTIAL</h3>
    <p class="service-text">Sed ut perspiciatis unde omnis iste natus<br>error sit voluptatem accusantium doloremque<br>laudantium, totam rem aperiam</p>
  </div>
  <div class="service" style="left:450px">
    <svg class="service-icon" viewBox="0 0 122 122"><circle cx="61" cy="61" r="59" fill="var(--gold)"/><circle cx="61" cy="61" r="54" fill="var(--navy)"/>
      <rect x="48" y="34" width="26" height="50" fill="#fff"/>
      <g fill="var(--navy)"><rect x="52" y="40" width="5" height="5"/><rect x="65" y="40" width="5" height="5"/><rect x="52" y="50" width="5" height="5"/><rect x="65" y="50" width="5" height="5"/><rect x="52" y="60" width="5" height="5"/><rect x="65" y="60" width="5" height="5"/><rect x="57" y="72" width="8" height="12"/></g></svg>
    <h3 class="service-name">COMMERCIAL</h3>
    <p class="service-text">Sed ut perspiciatis unde omnis iste natus<br>error sit voluptatem accusantium doloremque<br>laudantium, totam rem aperiam</p>
  </div>
  <div class="service" style="left:802px">
    <svg class="service-icon" viewBox="0 0 122 122"><circle cx="61" cy="61" r="59" fill="var(--gold)"/><circle cx="61" cy="61" r="54" fill="var(--navy)"/>
      <path d="M41 58 Q41 38 61 38 Q81 38 81 58 Z" fill="#fff"/><rect x="37" y="58" width="48" height="5" fill="#fff"/>
      <path d="M40 86 Q40 72 61 72 Q82 72 82 86 Z" fill="#fff"/></svg>
    <h3 class="service-name">OTHER</h3>
    <p class="service-text">Sed ut perspiciatis unde omnis iste natus<br>error sit voluptatem accusantium doloremque<br>laudantium, totam rem aperiam</p>
  </div>
</section>

<section class="projects">
  <div class="projects-bg" role="img" aria-label="Dark toned view of a construction site with building frames"></div>
  <h2 class="abs center section-title projects-title">RECENT PROJECTS</h2>
  <p class="abs center section-sub projects-sub">Sed ut perspiciatis unde omnis iste natus error sit voluptatem accusantium doloremque laudantium, totam rem aperiam</p>

  <svg class="abs slider-arrow" style="left:36px" viewBox="0 0 24 80"><polyline points="20,2 4,40 20,78" fill="none" stroke="#fff" stroke-width="1.6"/></svg>
  <svg class="abs slider-arrow" style="left:1140px" viewBox="0 0 24 80"><polyline points="4,2 20,40 4,78" fill="none" stroke="#fff" stroke-width="1.6"/></svg>

  <article class="project-card" style="left:84px">
    <div class="project-photo" role="img" aria-label="Workers on a building frame against a sunset sky" style="background:linear-gradient(180deg,#3a5f8f 0%,#d98a3c 60%,#6b3a1e 100%)"></div>
    <div class="project-caption"><p class="project-name">SED UT PERSPICIATIS</p><p class="project-meta">Nemo enim ipsam voluptatem</p>
      <svg class="project-plus" viewBox="0 0 58 66"><path d="M29 24v18M20 33h18" stroke="#fff" stroke-width="4"/></svg></div>
  </article>
  <article class="project-card" style="left:345px">
    <div class="project-photo" role="img" aria-label="Architectural plans and tools on a table" style="background:linear-gradient(180deg,#b88a4a 0%,#e9dcc6 55%,#cfc6b5 100%)"></div>
    <div class="project-caption"><p class="project-name">SED UT PERSPICIATIS</p><p class="project-meta">Nemo enim ipsam voluptatem</p>
      <svg class="project-plus" viewBox="0 0 58 66"><path d="M29 24v18M20 33h18" stroke="#fff" stroke-width="4"/></svg></div>
  </article>
  <article class="project-card" style="left:605px">
    <div class="project-photo" role="img" aria-label="Site engineers reviewing an interior build" style="background:linear-gradient(180deg,#d9d5cf 0%,#b7a999 55%,#8a7a68 100%)"></div>
    <div class="project-caption"><p class="project-name">SED UT PERSPICIATIS</p><p class="project-meta">Nemo enim ipsam voluptatem</p>
      <svg class="project-plus" viewBox="0 0 58 66"><path d="M29 24v18M20 33h18" stroke="#fff" stroke-width="4"/></svg></div>
  </article>
  <article class="project-card" style="left:867px">
    <div class="project-photo" role="img" aria-label="Surveyor with tower cranes on a building site" style="background:linear-gradient(180deg,#9fc0dd 0%,#d8c79a 60%,#b86a3a 100%)"></div>
    <div class="project-caption"><p class="project-name">SED UT PERSPICIATIS</p><p class="project-meta">Nemo enim ipsam voluptatem</p>
      <svg class="project-plus" viewBox="0 0 58 66"><path d="M29 24v18M20 33h18" stroke="#fff" stroke-width="4"/></svg></div>
  </article>
</section>

<section class="about">
  <div class="abs about-photo" role="img" aria-label="Builder in a hard hat shaking hands over building plans"></div>
  <h2 class="abs section-title about-title">ABOUT US</h2>
  <p class="abs about-kicker">SED UT PERSPICIATIS UNDE OMNIS ISTE NATUS ERROR SIT</p>
  <p class="abs about-text">Nemo enim ipsam voluptatem quia voluptas sit aspernatur aut odit aut fugit, sed<br>quia consequuntur magni dolores eos qui ratione voluptatem sequi nesciunt. Neq<br>ue porro quisquam est, qui dolorem ipsum quia dolor sit amet, consectetur, adip<br>isci velit, sed quia non numquam eius modi tempora incidunt Sed ut perspiciatis<br>totam rem aperiam,eaque ipsa quae ab illo inventore veritatis</p>
  <a class="abs btn about-btn">READ MORE</a>
</section>

<footer>
  <div class="site-footer"></div>
  <div class="footer-col" style="left:126px">
    <h4 class="footer-heading">QUICK LINKS</h4>
    <ul class="link-list">
      <li><svg width="8" height="8" viewBox="0 0 8 8"><path d="M1 1l3 3-3 3M4 1l3 3-3 3" fill="none" stroke="#666"/></svg>Home</li>
      <li><svg width="8" height="8" viewBox="0 0 8 8"><path d="M1 1l3 3-3 3M4 1l3 3-3 3" fill="none" stroke="#666"/></svg>About us</li>
      <li><svg width="8" height="8" viewBox="0 0 8 8"><path d="M1 1l3 3-3 3M4 1l3 3-3 3" fill="none" stroke="#666"/></svg>Projects</li>
      <li><svg width="8" height="8" viewBox="0 0 8 8"><path d="M1 1l3 3-3 3M4 1l3 3-3 3" fill="none" stroke="#666"/></svg>Blog</li>
      <li><svg width="8" height="8" viewBox="0 0 8 8"><path d="M1 1l3 3-3 3M4 1l3 3-3 3" fill="none" stroke="#666"/></svg>Contact us</li>
    </ul>
  </div>
  <div class="footer-col" style="left:343px">
    <h4 class="footer-heading">CONTACT US</h4>
    <ul class="contact-list">
      <li><svg width="14" height="12" viewBox="0 0 14 12"><path d="M1 4Q7 -1 13 4L11 6 9 4H5L3 6Z M3 7h8v4H3z" fill="#666"/></svg>(000)-121-1231 (Phone)</li>
      <li><svg width="14" height="12" viewBox="0 0 14 12"><rect x="3" y="0" width="8" height="4" fill="#666"/><rect x="1" y="4" width="12" height="6" rx="1" fill="#666"/></svg>(000)-121-1231 (Fax)</li>
      <li><svg width="14" height="12" viewBox="0 0 14 12"><rect x="1" y="2" width="12" height="8" fill="none" stroke="#666"/><path d="M1 2l6 5 6-5" fill="none" stroke="#666"/></svg><a>info@keltoconstruction.example.com</a></li>
      <li><svg width="14" height="14" viewBox="0 0 14 14"><path d="M7 1a4 4 0 0 1 4 4c0 3-4 8-4 8S3 8 3 5a4 4 0 0 1 4-4z" fill="#666"/></svg>70 Lorem Ipsum Dummy Text<br>Lorem Ipsum</li>
    </ul>
  </div>
  <div class="footer-col" style="left:615px">
    <h4 class="footer-heading">NEWSLETTER</h4>
    <p class="footer-text">Register Your email address to get<br>information abtout us</p>
    <div class="newsletter-input">Email Address</div>
    <div class="btn subscribe-btn">SUBSCRIBE</div>
  </div>
  <div class="footer-col" style="left:893px">
    <h4 class="footer-heading">FOLLOW US</h4>
    <p class="footer-text">Lorem ipsum dolor sit amet, conse<br>ctetur adipiscing elit. Nulla in purus<br>nibh. Donec ornare</p>
    <div class="socials">
      <span class="social" aria-label="Social profile"></span><span class="social" aria-label="Social profile"></span><span class="social" aria-label="Social profile"></span><span class="social" aria-label="Social profile"></span><span class="social" aria-label="Social profile"></span>
    </div>
  </div>
  <div class="bottom-bar"></div>
  <p class="abs center copyright">© Copyright 2018 Kelto Construction.All Rights Reserved</p>
</footer>

</body>
</html>
```